Brindle Sky Port needs a new upscale business card design for our high end aircraft hangar complex

Brindle Sky Port (BSP) is a large, upscale jet hangar complex in the US housing expensive aircraft. We need a new business card design, using our current logo. We will be attending a industry convention and need a card design that will stand out and be remembered by aircraft owners and private pilots.

Target Market(s)

Aircraft pilots or owners looking for a new upscale hangar

Industry/Entity Type

Airport

Contact Information for Business Card

I like to use very heavy card stock, 400#, double sided. Square, no rounded edges please.

Colors
3276b5
0255a3
85abd2

Requirements
Must have
• An expensive, classy design, vivid colors.
Nice to have
• Needs to look very expensive and classy, and have some "pop". Designer must be able to download or copy my current typeface or fonts.
• One card side might be black with the "Logo and Brindle Sky Port Double line image in blue (or try gold, or glossy black), and perhaps have a grayed out "K720 jet silhouette". The other card side would have our contact info, and perhaps the "BSP Logo only". I'd like my contact info 'stacked', not in a paragraph format.
Should not have
• Should not look "too busy". Having a double-sided card will help.

```html
<!DOCTYPE html>
<html lang="en">
<head>
<meta charset="utf-8">
<title>Brindle Sky Port — Business Card</title>
<link rel="stylesheet" href="https://fonts.googleapis.com/css2?family=Source+Sans+3:wght@400;600&display=swap">
<style>
  :root {
    --page: #2a2b2d;
    --card: #111214;
    --card-edge: #1b1c1f;
    --blue: #3276b5;
    --blue-deep: #0255a3;
    --blue-light: #85abd2;
    --text: #e9ecef;
    --muted: #b9c0c7;
    --ghost: rgba(50, 118, 181, 0.07);
  }
  * { box-sizing: border-box; margin: 0; padding: 0; }
  html, body {
    width: 1200px; height: 950px; overflow: hidden;
    background: var(--page);
    font-family: "Source Sans 3", "Myriad Pro", Arial, sans-serif;
  }
  .sheet {
    width: 1200px; height: 950px;
    display: flex; flex-direction: column;
    align-items: center; justify-content: center; gap: 50px;
  }
  .card {
    position: relative;
    width: 700px; height: 400px;
    background: linear-gradient(160deg, var(--card-edge), var(--card) 60%);
    border-radius: 14px;
    overflow: hidden;
    box-shadow: 0 8px 24px rgba(0,0,0,0.45);
  }

  /* Contact side */
  .accent-bar {
    position: absolute; height: 12px; width: 320px;
    background: linear-gradient(90deg, var(--blue-deep), var(--blue), var(--blue-deep));
  }
  .accent-bar--top { top: 0; left: 0; border-bottom-right-radius: 6px; }
  .accent-bar--bottom { bottom: 0; right: 0; border-top-left-radius: 6px; }
  .ghost-mark {
    position: absolute; left: 50%; top: 50%;
    transform: translate(-50%, -50%);
    font-size: 230px; font-weight: 600; letter-spacing: 10px;
    color: var(--ghost);
    line-height: 1;
    user-select: none;
  }
  .contact {
    position: absolute; inset: 0;
    display: flex; flex-direction: column; align-items: center; justify-content: center;
    text-align: center;
  }
  .contact__name {
    color: var(--blue); font-size: 30px; font-weight: 600; letter-spacing: 1px;
    text-transform: uppercase;
  }
  .contact__role { color: var(--muted); font-size: 19px; margin-bottom: 34px; }
  .contact__line { color: var(--text); font-size: 18px; line-height: 1.55; }
  .label { color: var(--blue); font-weight: 600; margin-right: 4px; }
  .sep { display: inline-block; width: 12px; }

  /* Brand side */
  .aircraft-shade {
    position: absolute; inset: 0;
    background: radial-gradient(ellipse at 35% 30%, #2a2c30 0%, #1a1b1e 40%, var(--card) 75%);
  }
  .brand {
    position: absolute; left: 0; right: 0; bottom: 70px;
    display: flex; align-items: center; justify-content: center; gap: 16px;
  }
  .brand__square { width: 22px; height: 22px; background: var(--blue); }
  .brand__name {
    color: var(--blue); font-size: 46px; font-weight: 600;
    letter-spacing: 3px; text-transform: uppercase;
  }
</style>
</head>
<body>
<main class="sheet">
  <section class="card card--contact">
    <div class="accent-bar accent-bar--top"></div>
    <div class="accent-bar accent-bar--bottom"></div>
    <div class="ghost-mark" aria-hidden="true">BSP</div>
    <div class="contact">
      <p class="contact__name">Dana Whitfield</p>
      <p class="contact__role">CEO / Founder</p>
      <p class="contact__line">1420 Harbor Crest Road, Juneau, Alaska 99801</p>
      <p class="contact__line">
        <span class="label">P</span>(555) 214-7730<span class="sep"></span>
        <span class="label">C</span>(555) 309-4182<span class="sep"></span>
        <span class="label">F</span>(555) 871-6025
      </p>
      <p class="contact__line">
        <span class="label">E</span>dana@brindlesky.com<span class="sep"></span>
        <span class="label">W</span>brindlesky.com
      </p>
    </div>
  </section>

  <section class="card card--brand">
    <div class="aircraft-shade" role="img" aria-label="Faint grey silhouette of a K720 jet on black"></div>
    <div class="brand">
      <span class="brand__square" aria-hidden="true"></span>
      <span class="brand__name">Brindle Sky Port</span>
    </div>
  </section>
</main>
</body>
</html>
```